4th Generation Family Business Needs a New Card Design!

We are a family owned 4th Generation company. We are based in the Sydney, Australia area and we are desperately in need of a more modern and classy card. We are monumental masons who design, supply & erect lasting memorials throughout cemeteries in Sydney. Our customers are normally in a period of grieving. I have attached logo files that will need to be implemented on the card. Company was established 1935. Australian Owned and Operated. Card needs to be designed to PIXO.com specification.

Target Market(s)

Our target market is based upon people that a grieving for family members that have passed away. We also deal with alot of companies that own and operate cemeteries.

Industry/Entity Type

Business

Contact Information for Business Card

Simon Harcourt, Operations Manager, 0417293086, simon@harcourtmemorials.com.au
Lewis Harcourt, Director, 0491630572, lewis@harcourtmemorials.com.au
Phone # 02 9561 3048
Website: www.harcourtmemorials.com.au
Address: Suite 17, 8 Palfrey Lane, West Carlow, Sydney NSW 2156

Font styles to use
Serif
Decorative
Script

Requirements
Must have
• Would like to see the logo nicely implemented with a modern design. Embossed lettering would be a nice additive.

```html
<!DOCTYPE html>
<html lang="en">
<head>
<meta charset="utf-8">
<title>Harcourt Memorials – Business Card</title>
<link rel="stylesheet" href="https://fonts.googleapis.com/css2?family=Merriweather:wght@400;700&display=swap">
<style>
  :root {
    --backdrop: #d9d4cc;
    --card-black: #111111;
    --ink-white: #f4f4f4;
    --gold: #d9c12a;
    --gold-deep: #b9a21c;
    --rule-gold: #8f7d16;
  }
  * { box-sizing: border-box; margin: 0; padding: 0; }
  html, body {
    width: 1200px; height: 780px; overflow: hidden;
    background: var(--backdrop);
    font-family: "Merriweather", Georgia, serif;
  }
  .canvas { position: relative; width: 1200px; height: 780px; }

  .card {
    position: absolute;
    background: var(--card-black);
    border-radius: 22px;
    overflow: hidden;
    box-shadow: 0 10px 24px rgba(0,0,0,.25);
  }

  /* Front */
  .card-front {
    left: 90px; top: 90px; width: 350px; height: 600px;
    display: flex; flex-direction: column; align-items: center;
    color: var(--ink-white); text-align: center;
  }
  .brand {
    margin-top: 64px;
    display: flex; flex-direction: column; align-items: center; gap: 10px;
  }
  .brand-name {
    font-weight: 700; font-size: 30px; letter-spacing: 3px;
    color: var(--ink-white); text-transform: uppercase; line-height: 1.15;
  }
  .brand-rule { width: 250px; height: 2px; background: var(--gold); }

  .person { margin-top: 34px; }
  .person-name {
    font-weight: 700; font-size: 19px; letter-spacing: 2px; text-transform: uppercase;
  }
  .person-role { color: var(--gold); font-weight: 700; font-size: 15px; margin-top: 4px; }

  .contact-list { margin-top: 20px; width: 270px; }
  .contact-item {
    padding: 8px 0;
    border-top: 1px solid var(--rule-gold);
  }
  .contact-label { color: var(--gold); font-weight: 700; font-size: 11px; }
  .contact-value { font-weight: 700; font-size: 15px; margin-top: 2px; letter-spacing: .5px; }
  .contact-value.email { font-size: 12px; letter-spacing: 0; }

  .address { margin-top: 14px; font-weight: 700; font-size: 13px; line-height: 1.5; }

  .web-band {
    position: absolute; left: 0; right: 0; bottom: 0; height: 72px;
    background: var(--gold);
    display: flex; align-items: center; justify-content: center;
    color: var(--card-black); font-weight: 700; font-size: 13px;
  }

  /* Back */
  .card-back {
    left: 520px; top: 215px; width: 600px; height: 350px;
    display: flex; flex-direction: column; align-items: center; justify-content: center;
    gap: 16px;
  }
  .back-web { color: var(--gold); font-size: 12px; font-weight: 700; letter-spacing: .5px; }
  .back-brand-row { display: flex; align-items: center; gap: 18px; }
  .back-rule { width: 60px; height: 2px; background: var(--gold); }
  .back-brand {
    font-weight: 700; font-size: 40px; letter-spacing: 5px;
    color: var(--ink-white); text-transform: uppercase; text-align: center; line-height: 1.2;
  }
</style>
</head>
<body>
<main class="canvas">

  <section class="card card-front" aria-label="Card front">
    <div class="brand">
      <div class="brand-name">Harcourt<br>Memorials</div>
      <div class="brand-rule"></div>
    </div>

    <div class="person">
      <div class="person-name">Simon Harcourt</div>
      <div class="person-role">Operations Manager</div>
    </div>

    <div class="contact-list">
      <div class="contact-item">
        <div class="contact-label">Mobile</div>
        <div class="contact-value">0417293086</div>
      </div>
      <div class="contact-item">
        <div class="contact-label">Phone</div>
        <div class="contact-value">02 9561 3048</div>
      </div>
      <div class="contact-item">
        <div class="contact-label">Email</div>
        <div class="contact-value email">simon@harcourtmemorials.com.au</div>
      </div>
    </div>

    <p class="address">Suite 17, 8 Palfrey Lane,<br>West Carlow, Sydney NSW 2156</p>

    <div class="web-band">www.harcourtmemorials.com.au</div>
  </section>

  <section class="card card-back" aria-label="Card back">
    <div class="back-brand-row">
      <div class="back-rule"></div>
      <div class="back-brand">Harcourt<br>Memorials</div>
      <div class="back-rule"></div>
    </div>
    <div class="back-web">www.harcourtmemorials.com.au</div>
  </section>

</main>
</body>
</html>
```